Velvet Riot Rising Line of Sparkling Wine & Spirits

Back info: Nora Beth Quill Owner 555-318-4402 1480 E. Harlow Ave, Bldg. 2, & 3, Fenwick Ca. 95871
Sparkling Wines & Memorabilia www.velvetriotrising.com
Ok I have uploaded the winning design. The color that I am after is the Fushia, Raspberry, Red, Matte Satin Matalic Finish. With a 24 Karet Gold color Foil. The Bottle is on the top row and it's the 2nd Bottle in. That is the Color that I want. This is the style of font. Make sure that you put what we're advertising. Good Luck to you all. Warmest regards, Nora
21 & up UniSex
Sparkling Wine and Memorabilia
there listed up above.....

```html
<!DOCTYPE html>
<html lang="en">
<head>
<meta charset="utf-8">
<title>Velvet Riot Rising – Business Card</title>
<link href="https://fonts.googleapis.com/css2?family=Arimo:wght@400;700&display=swap" rel="stylesheet">
<style>
  :root {
    --raspberry: #c8137a;
    --raspberry-deep: #8e0f55;
    --raspberry-bright: #e0248f;
    --gold: #e2a53c;
    --ink: #444444;
    --paper: #ffffff;
    --backdrop: #e4e4e4;
    --grey-dark: #5f5f5f;
  }
  * { margin: 0; padding: 0; box-sizing: border-box; }
  html, body {
    width: 1200px; height: 1200px; overflow: hidden;
    background: var(--backdrop);
    font-family: "Arimo", Arial, sans-serif;
  }
  .canvas { position: relative; width: 1200px; height: 1200px; }
  .card {
    position: absolute;
    width: 803px; height: 458px;
    transform: scale(0.857);
    transform-origin: top left;
    background: var(--paper);
    overflow: hidden;
    box-shadow: 0 18px 30px rgba(0,0,0,0.25);
  }
  .card--front { left: 267px; top: 159px; }
  .card--back { left: 262px; top: 654px; }

  .front-swoosh { position: absolute; inset: 0; width: 803px; height: 458px; }

  .bottle {
    position: absolute;
    border-radius: 14px 14px 10px 10px;
    background: linear-gradient(90deg, var(--raspberry-deep), var(--raspberry-bright) 45%, var(--raspberry) 70%, var(--raspberry-deep));
  }
  .card--front .bottle { left: 50px; top: 32px; width: 80px; height: 266px; }
  .card--back .bottle { left: 359px; top: 67px; width: 82px; height: 282px; }

  .holder { position: absolute; right: 78px; top: 162px; text-align: right; }
  .holder__name {
    color: var(--raspberry); font-weight: 700; font-size: 32px; letter-spacing: 0.3px;
  }
  .holder__title { color: var(--gold); font-size: 20px; margin-top: 2px; }

  .contact { position: absolute; left: 52px; top: 316px; color: var(--ink); font-size: 18.5px; line-height: 25px; }
  .contact__address { margin-bottom: 14px; }
  .contact__row { display: flex; align-items: center; gap: 14px; height: 23px; }
  .contact__icon { width: 16px; height: 16px; flex: none; }

  .back-fade {
    position: absolute; inset: 0;
    background: linear-gradient(180deg, var(--paper) 0%, var(--paper) 45%, #d9d9d9 58%, #9a9a9a 80%, var(--grey-dark) 100%);
  }
  .back-rule {
    position: absolute; left: 164px; top: 349px; width: 480px; height: 1px;
    background: linear-gradient(90deg, transparent, #555 20%, #555 80%, transparent);
  }
  .tagline {
    position: absolute; left: 0; right: 0; top: 382px; text-align: center;
    font-size: 20px; letter-spacing: 4.6px; color: #111;
  }
  .tagline strong { font-weight: 700; }
</style>
</head>
<body>
<main class="canvas">

  <section class="card card--front">
    <svg class="front-swoosh" viewBox="0 0 803 458" aria-hidden="true">
      <defs>
        <linearGradient id="bronzeFill" x1="0" y1="0" x2="1" y2="1">
          <stop offset="0" stop-color="#6e4318"/>
          <stop offset="1" stop-color="#a8733a"/>
        </linearGradient>
        <linearGradient id="raspberryFill" x1="0" y1="0" x2="0" y2="1">
          <stop offset="0" stop-color="#9c1060"/>
          <stop offset="0.5" stop-color="#d4187f"/>
          <stop offset="1" stop-color="#8e0f55"/>
        </linearGradient>
      </defs>
      <rect x="560" y="0" width="243" height="458" fill="url(#bronzeFill)"/>
      <path d="M725,60 C790,130 806,220 803,300 L803,458 L570,458 C700,400 790,300 725,60 Z"
            fill="url(#raspberryFill)" stroke="#ffffff" stroke-width="4"/>
      <path d="M0,0 L650,0 C770,35 800,170 770,280 C740,380 660,430 580,458 L0,458 Z" fill="#ffffff"/>
    </svg>

    <div class="bottle" role="img" aria-label="Raspberry sparkling wine bottle with gold foil neck and brand label"></div>

    <div class="holder">
      <div class="holder__name">NORA BETH QUILL</div>
      <div class="holder__title">Owner</div>
    </div>

    <div class="contact">
      <div class="contact__address">E. Harlow Ave<br>Bldg. 2, &amp; 3, Fenwick Ca. 95871</div>
      <div class="contact__row">
        <svg class="contact__icon" viewBox="0 0 24 24" aria-hidden="true"><path fill="#c8137a" d="M6.6 10.8a15.2 15.2 0 0 0 6.6 6.6l2.2-2.2c.3-.3.7-.4 1-.2 1.1.4 2.3.6 3.6.6.6 0 1 .4 1 1V20c0 .6-.4 1-1 1A17 17 0 0 1 3 4c0-.6.4-1 1-1h3.5c.6 0 1 .4 1 1 0 1.3.2 2.5.6 3.6.1.3 0 .7-.2 1z"/></svg>
        <span>555-318-4402 1480</span>
      </div>
      <div class="contact__row">
        <svg class="contact__icon" viewBox="0 0 24 24" aria-hidden="true"><circle cx="12" cy="12" r="10" fill="#c8137a"/><path fill="#fff" d="M8 6c2 0 3 1 2.5 2.5S8 10 8.5 12s2 2 1.5 4-2 2-3 1.5A8 8 0 0 1 8 6zm7 1c1.5.5 3 2 3.5 4-1 .5-2 0-2.5-1s-1.5-1-1-3z"/></svg>
        <span>www.velvetriotrising.com</span>
      </div>
    </div>
  </section>

  <section class="card card--back">
    <div class="back-fade"></div>
    <div class="bottle" role="img" aria-label="Raspberry sparkling wine bottle with gold foil neck and brand label"></div>
    <div class="back-rule"></div>
    <p class="tagline">SPARKLING <strong>WINES &amp; MEMORABILIA</strong></p>
  </section>

</main>
</body>
</html>
```